Harbor Loom Floors Letterhead

Letterhead used for business reasons. It must be editable and easy to use.

Address is 2715 W. Pelican Lane Englewood FL 34187 - 941.382.6519

```html
<!DOCTYPE html>
<html lang="en">
<head>
<meta charset="utf-8">
<title>Harbor Loom Floors Letterhead</title>
<link href="https://fonts.googleapis.com/css2?family=Montserrat:wght@400;500;700&family=Kaushan+Script&display=swap" rel="stylesheet">
<style>
  :root {
    --backdrop: #e4e4e6;
    --paper: #ffffff;
    --ink: #1d1d1d;
    --ink-soft: #444444;
    --orange: #e28c28;
    --taupe: #958a86;
  }
  * { box-sizing: border-box; margin: 0; padding: 0; }
  html, body {
    width: 1200px; height: 874px; overflow: hidden;
    background: var(--backdrop);
    font-family: "Montserrat", sans-serif;
  }
  .letterhead {
    position: absolute; left: 291px; top: 0;
    width: 618px; height: 874px;
    background: var(--paper);
    overflow: hidden;
  }
  .brand {
    position: absolute; left: 52px; top: 64px;
    display: flex; align-items: center; gap: 9px;
    font-size: 19px; font-weight: 500; color: var(--orange);
    letter-spacing: 0.3px;
  }
  .brand-dot { width: 12px; height: 12px; border-radius: 50%; background: var(--orange); }
  .contact {
    position: absolute; left: 440px; top: 52px;
    font-style: normal;
    font-size: 8.5px; line-height: 1.55; color: var(--ink-soft);
    padding-left: 14px;
  }
  .contact::before {
    content: ""; position: absolute; left: 0; top: 10px;
    width: 1.5px; height: 38px; background: var(--orange);
  }
  .contact .phone { display: flex; align-items: center; gap: 4px; }
  .letter {
    position: absolute; left: 52px; top: 172px; width: 470px;
    font-size: 10.2px; line-height: 1.45; color: var(--ink);
    z-index: 1;
  }
  .date { margin-bottom: 22px; }
  .recipient { margin-bottom: 22px; }
  .company { margin-bottom: 28px; }
  .salutation { font-weight: 700; font-size: 12.5px; margin-bottom: 22px; }
  .letter p.body { margin-bottom: 15px; }
  .closing { margin-top: 18px; }
  .signature {
    font-family: "Kaushan Script", cursive;
    font-size: 27px; margin-top: 30px; margin-left: 40px;
  }
  .corner-wave { position: absolute; left: 0; top: 0; width: 618px; height: 874px; }
</style>
</head>
<body>
  <main class="letterhead">
    <div class="brand"><span class="brand-dot"></span>Harbor Loom Floors</div>

    <address class="contact">
      <div>2715 W. Pelican Lane</div>
      <div>Englewood FL 34187</div>
      <div class="phone">
        <svg width="8" height="8" viewBox="0 0 24 24" aria-hidden="true"><path fill="var(--orange)" d="M6.6 10.8a15.1 15.1 0 0 0 6.6 6.6l2.2-2.2a1 1 0 0 1 1-.25 11.4 11.4 0 0 0 3.6.57 1 1 0 0 1 1 1V20a1 1 0 0 1-1 1A17 17 0 0 1 3 4a1 1 0 0 1 1-1h3.5a1 1 0 0 1 1 1c0 1.25.2 2.45.57 3.57a1 1 0 0 1-.25 1z"/></svg>
        941.382.6519
      </div>
    </address>

    <section class="letter">
      <div class="date">January-03-2020</div>
      <div class="recipient">Mr. Adam Lowe<br>President</div>
      <div class="company">Brightway Holdings<br>123 Street Name, Suite# 10<br>City, State, 120023</div>
      <div class="salutation">Dear Mr. Lowe</div>
      <p class="body">Lorem ipsum dolor sit amet, consectetur adipiscing elit, sed do eiusmod tempor incididunt ut labore et dolore magna aliqua. Ut enim ad minim veniam, quis nostrud exercitation ullamco laboris nisi ut aliquip ex ea commodo consequat. Duis aute irure dolor in reprehenderit in voluptate velit esse cillum dolore eu fugiat nulla pariatur.</p>
      <p class="body">Lorem ipsum dolor sit amet, consectetur adipiscing elit, sed do eiusmod tempor incididunt ut labore et dolore magna aliqua. Ut enim ad minim veniam, quis nostrud exercitation ullamco laboris nisi ut aliquip ex ea commodo consequat. Duis aute irure dolor in reprehenderit in voluptate velit esse cillum dolore eu fugiat nulla pariatur.</p>
      <p class="body">Lorem ipsum dolor sit amet, consectetur adipiscing elit, sed do eiusmod tempor incididunt ut labore et dolore magna aliqua. Ut enim ad minim veniam, quis nostrud exercitation ullamco laboris nisi ut aliquip ex ea commodo consequat.</p>
      <p class="body">Excepteur sint occaecat cupidatat non proident, sunt in culpa qui officia deserunt mollit anim id est laborum. re et dolore magnam aliquam quaerat voluptatem.</p>
      <div class="closing">Regards</div>
      <div class="signature">Daniel Reyes</div>
    </section>

    <svg class="corner-wave" viewBox="0 0 618 874" role="img" aria-label="Decorative orange and taupe wave across the bottom right corner of the page">
      <defs>
        <linearGradient id="wave-tone" x1="0.2" y1="0" x2="0.8" y2="1">
          <stop offset="0" stop-color="var(--taupe)"/>
          <stop offset="0.35" stop-color="var(--orange)"/>
          <stop offset="1" stop-color="var(--orange)"/>
        </linearGradient>
      </defs>
      <path fill="url(#wave-tone)" d="M262 874 C 390 760, 560 690, 618 505 L 618 874 Z"/>
    </svg>
  </main>
</body>
</html>
```